Business Card Design for Brindle Consulting

I need business cards for a new company I have started called Brindle Consulting. Brindle Consulting is a new business based out of Columbus Ohio. I will be operating in Ohio as well as nationwide. Brindle Consulting is a professional organization designed to fit your organization's specific needs. We are dedicated to the success of organizations. We handle human resource management, leadership coaching and development, executive training, team building, personality inventories and searches, performance evaluations, temp. services, custom solutions and more. Brindle consulting services a variety of industries such as government agencies, educational systems, board of directors, construction services and more, please visit our website for a full list of services (the website will be important).

I leave the design to you. I am a 45 year old male. I was in the education field for 21 years and 11 years as a superintendent. I like the colors red and black. Don't know what works, I will leave that to you as well. I would like to have it be catchy yet masculine. I have been associated with many organizations over the years both public and private, and will be reaching out to the public and private sector.

I do need a logo...so I leave that to you as well. Company name is Brindle Consulting.

Industry/Entity Type

Construction

Contact Information for Business Card

Gordon T. Brindle, President
Brindle Consulting
48 W.Fifth St. Suite 305
Arcade at Halvern Court
Columbus, Ohio 43287

Phone : 330-555-4178
email : gbrindle@brindleadvise.example
web : www.brindleadvise.example
twitter : @brindleadvise
facebook : Brindle Consulting

```html
<!DOCTYPE html>
<html lang="en">
<head>
<meta charset="utf-8">
<title>Brindle Consulting – Business Card</title>
<link href="https://fonts.googleapis.com/css2?family=Jura:wght@500;600;700&display=swap" rel="stylesheet">
<style>
  :root {
    --backdrop: #2b2c2e;
    --card-white: #f7f7f7;
    --brand-blue: #0aa8e8;
    --charcoal: #333436;
    --ink: #1e1f21;
  }
  html, body {
    margin: 0;
    width: 1200px;
    height: 816px;
    overflow: hidden;
    background: var(--backdrop);
  }
  .canvas {
    position: relative;
    width: 1200px;
    height: 816px;
  }
  .business-card {
    position: absolute;
    left: 100px;
    top: 123px;
    width: 1000px;
    height: 571px;
    border-radius: 34px;
    overflow: hidden;
    background: var(--brand-blue);
    font-family: "Jura", sans-serif;
    color: var(--ink);
  }
  .card-shapes {
    position: absolute;
    inset: 0;
  }
  .company-name {
    position: absolute;
    right: 40px;
    top: 50%;
    transform: translate(50%, -50%) rotate(90deg);
    margin: 0 30px 0 0;
    white-space: nowrap;
    font-size: 30px;
    font-weight: 600;
    letter-spacing: 3px;
    text-transform: uppercase;
    color: var(--ink);
  }
  .rule {
    position: absolute;
    height: 5px;
    background: var(--brand-blue);
  }
  .rule--top { left: 150px; top: 168px; width: 390px; }
  .rule--bottom { left: 60px; top: 298px; width: 480px; }
  .icon {
    position: absolute;
    left: 78px;
    width: 46px;
    height: 46px;
    border-radius: 50%;
    background: var(--brand-blue);
  }
  .icon svg { position: absolute; inset: 0; }
  .line {
    position: absolute;
    left: 150px;
    margin: 0;
    font-size: 22px;
    font-weight: 600;
    line-height: 1.15;
    letter-spacing: 1px;
    white-space: nowrap;
  }
  .holder-name { top: 198px; font-size: 29px; letter-spacing: 1.5px; text-transform: uppercase; }
  .holder-title { top: 234px; font-size: 25px; letter-spacing: 2px; }
</style>
</head>
<body>
<div class="canvas">
  <div class="business-card">
    <svg class="card-shapes" width="1000" height="571" viewBox="0 0 1000 571" aria-hidden="true">
      <polygon fill="var(--charcoal)" points="0,0 640,0 735,190 735,340 600,571 0,571"/>
      <polygon fill="var(--card-white)" points="0,0 560,0 660,190 660,350 530,571 0,571"/>
    </svg>

    <p class="company-name">Brindle Consulting</p>

    <div class="rule rule--top"></div>
    <div class="icon" style="top:207px">
      <svg viewBox="0 0 46 46" aria-hidden="true">
        <circle cx="23" cy="18" r="6" fill="#fff"/>
        <path d="M12 34c1-7 5-10 11-10s10 3 11 10z" fill="#fff"/>
      </svg>
    </div>
    <p class="line holder-name">Gordon T. Brindle</p>
    <p class="line holder-title">President</p>
    <div class="rule rule--bottom"></div>

    <div class="icon" style="top:333px">
      <svg viewBox="0 0 46 46" aria-hidden="true">
        <rect x="16" y="10" width="14" height="26" rx="2.5" fill="none" stroke="#fff" stroke-width="2.5"/>
        <circle cx="23" cy="31.5" r="1.6" fill="#fff"/>
      </svg>
    </div>
    <p class="line" style="top:330px">330-555-4178<br>@brindleadvise</p>

    <div class="icon" style="top:401px">
      <svg viewBox="0 0 46 46" aria-hidden="true">
        <rect x="11" y="13" width="24" height="16" rx="1.5" fill="none" stroke="#fff" stroke-width="2.5"/>
        <path d="M18 34h10M23 29v5" stroke="#fff" stroke-width="2.5"/>
      </svg>
    </div>
    <p class="line" style="top:398px">gbrindle@brindleadvise.example<br>www.brindleadvise.example</p>

    <div class="icon" style="top:481px">
      <svg viewBox="0 0 46 46" aria-hidden="true">
        <path d="M23 36c-6-8-9-12-9-17a9 9 0 0 1 18 0c0 5-3 9-9 17z" fill="#fff"/>
        <circle cx="23" cy="19" r="3.5" fill="var(--brand-blue)"/>
      </svg>
    </div>
    <p class="line" style="top:466px">48 W.Fifth St. Suite 305<br>Arcade at Halvern Court<br>Columbus, Ohio 43287</p>
  </div>
</div>
</body>
</html>
```